Willow Cradle Pregnancy and Baby Massage

I need a web design for a new business, WILLOW CRADLE PREGNANCY AND BABY MASSAGE that I am in the process of setting up in the suburbs of Perth, Western Australia. The business is owned and operated by myself and my intention is to service Pregnant Mothers and Parents of Young Babies that would benefit from massage. I would like to have a "Home Page" and pages for "About Me", "Pregnancy Massage", "Baby Massage", a Pricing Page for Pregnancy Massage Sessions, a Pricing Page for Baby Massage Sessions, and a "Contact Me" page to allow clients to either contact me with queries or book available pregnancy massage sessions on a particular day of the week. I would also like a "News" page that would include articles I have written, news about new courses and a link to my FamilyFeed page (yet to be set up). I would like to keep the colour schemes similar to my logo design colours. I need the design to be easy to follow and to appeal to a younger audience (20's to mid 30's).
The target audience is pregnant mothers-to-be wishing to receive massage treatments, and new parents and grandparents of small babies that would like to learn how to massage their babies.
The look and feel should be modern, professional, elegant and feminine.
I need the design to be in a standard format such that I can update the content by myself ( and does not need specialised software) as the company and business progresses.

Target Market(s)

Contact Information for Business Card

Card should have rounded edges. Design should have the same "feel" as the website. Contact Details of my business address, mobile phone, email and website should be included.

Font styles to use
Script

Requirements
Must have
• Same colours as logo design. In cmyk system, the colours are: 20,60,0,0 which best result is pantone 681 and 40,40,0,0 which best result is pantone 2645. Card should include the logo design.

```html
<!DOCTYPE html>
<html lang="en">
<head>
<meta charset="utf-8">
<title>About Me – Willow Cradle Pregnancy and Baby Massage</title>
<link rel="stylesheet" href="https://fonts.googleapis.com/css2?family=Questrial&family=Open+Sans:wght@400&display=swap">
<style>
  :root {
    --nav-bg: #403f44;
    --nav-text: #e6e3ea;
    --heading: #b7649f;
    --body-text: #4a4850;
    --lavender: #b3a0cb;
    --lavender-light: #c7c0df;
    --pink-soft: #e6c3dc;
    --brand-purple: #8a6aac;
    --dash: #444;
    --footer-bg: #4f4672;
    --footer-text: #d9d4ea;
    --band-pink: #f7e3ea;
    --badge: #c7a3cf;
  }
  * { box-sizing: border-box; margin: 0; padding: 0; }
  html, body { width: 1070px; height: 1200px; overflow: hidden; background: #fff; }
  body { position: relative; font-family: "Questrial", sans-serif; color: var(--body-text); }

  .top-nav {
    position: absolute; top: 0; left: 0; width: 1070px; height: 37px;
    background: var(--nav-bg); z-index: 2;
  }
  .top-nav ul { list-style: none; position: absolute; right: 117px; top: 11px; display: flex; gap: 24px; }
  .top-nav a { color: var(--nav-text); text-decoration: none; font-size: 11.5px; }
  .top-nav a.is-current { color: #fff; border-bottom: 1px solid #fff; padding-bottom: 1px; }

  .header-waves { position: absolute; top: 37px; left: 0; z-index: 1; }

  .brand-card {
    position: absolute; left: 118px; top: 0; width: 252px; height: 160px;
    background: #fff; border-radius: 0 0 22px 22px; z-index: 3;
    box-shadow: 0 3px 6px rgba(0,0,0,0.22);
  }
  .brand-card-inner {
    position: absolute; left: 7px; right: 7px; top: -2px; bottom: 8px;
    border: 1.5px dashed var(--dash); border-top: none; border-radius: 0 0 18px 18px;
    display: flex; align-items: center; justify-content: center; gap: 8px; padding: 0 12px;
  }
  .brand-dot { width: 14px; height: 14px; border-radius: 50%; background: var(--brand-purple); flex: none; }
  .brand-name { font-size: 17px; line-height: 1.3; color: var(--brand-purple); text-align: center; }

  .portrait-ring {
    position: absolute; left: 120px; top: 230px; width: 348px; height: 348px;
    border: 1.5px dashed var(--dash); border-radius: 50%;
  }
  .portrait-photo {
    position: absolute; left: 14px; top: 14px; width: 318px; height: 318px; border-radius: 50%;
    background: radial-gradient(circle at 50% 45%, #f4c4b0 0%, #eeb7a6 35%, #e9ddd6 75%, #dcd6d2 100%);
  }

  .about {
    position: absolute; left: 534px; top: 224px; width: 420px;
  }
  .about h1 { font-weight: 400; font-size: 28px; color: var(--heading); margin-bottom: 20px; }
  .about p { font-size: 16px; line-height: 27px; margin-bottom: 27px; }

  .hearts-band {
    position: absolute; left: 0; top: 914px; width: 1070px; height: 186px;
    background:
      radial-gradient(circle at 64% 35%, rgba(240,160,190,0.45) 0 14px, transparent 30px),
      radial-gradient(circle at 56% 75%, rgba(240,150,180,0.45) 0 16px, transparent 32px),
      radial-gradient(circle at 95% 25%, rgba(240,150,180,0.4) 0 12px, transparent 26px),
      radial-gradient(circle at 4% 85%, rgba(240,160,190,0.4) 0 12px, transparent 28px),
      linear-gradient(90deg, var(--band-pink), #f9eef2 50%, var(--band-pink));
  }
  .cert-badge {
    position: absolute; left: 128px; top: 944px; width: 100px; height: 128px;
    border-radius: 10px; background: var(--badge); opacity: 0.7;
  }
  .social {
    position: absolute; left: 850px; top: 974px; width: 124px; text-align: center;
  }
  .social-label { font-size: 14px; color: #444; margin-bottom: 10px; }
  .social-link { display: inline-flex; align-items: center; gap: 6px; font-size: 14px; color: var(--footer-bg); text-decoration: none; }
  .social-dot { width: 12px; height: 12px; border-radius: 50%; background: var(--footer-bg); }

  .site-footer {
    position: absolute; left: 0; top: 1100px; width: 1070px; height: 100px;
    background: var(--footer-bg); font-family: "Open Sans", sans-serif; text-align: center;
  }
  .footer-links { list-style: none; display: flex; justify-content: center; margin-top: 29px; font-size: 10.5px; }
  .footer-links li { color: var(--footer-text); }
  .footer-links li + li::before { content: "|"; margin: 0 9px; }
  .footer-links a { color: var(--footer-text); text-decoration: none; }
  .copyright { margin-top: 13px; font-size: 10.5px; color: var(--footer-text); }
</style>
</head>
<body>
  <nav class="top-nav">
    <ul>
      <li><a href="#">Home</a></li>
      <li><a href="#" class="is-current">About Me</a></li>
      <li><a href="#">Pregnancy Massage</a></li>
      <li><a href="#">Baby Massage</a></li>
      <li><a href="#">Pricing</a></li>
      <li><a href="#">News</a></li>
      <li><a href="#">Contact Me</a></li>
    </ul>
  </nav>

  <svg class="header-waves" width="1070" height="135" viewBox="0 0 1070 135" aria-hidden="true">
    <path d="M0 0 H1070 V130 C1000 90 960 60 900 45 C800 20 700 60 560 60 C400 60 250 40 0 60 Z" fill="var(--pink-soft)"/>
    <path d="M0 0 H1070 V25 C980 60 880 100 760 95 C620 90 500 40 360 55 C230 68 110 95 0 110 Z" fill="var(--lavender-light)"/>
    <path d="M0 0 H1070 V10 C960 30 880 50 760 50 C600 50 480 15 340 30 C200 45 100 55 0 60 Z" fill="var(--lavender)"/>
  </svg>

  <div class="brand-card">
    <div class="brand-card-inner">
      <span class="brand-dot"></span>
      <span class="brand-name">Willow Cradle Pregnancy and Baby Massage</span>
    </div>
  </div>

  <div class="portrait-ring">
    <div class="portrait-photo" role="img" aria-label="Photo of a newborn baby's feet resting in a parent's hand"></div>
  </div>

  <main class="about">
    <h1>About me</h1>
    <p>Maren is a Practitioner of Pregnancy Massage, and a Paediatric Massage Consultant. She completed her training with Prenatal Touch Institute, and the Infant Touch Learning Network. The ITLN is endorsed by the Coastal Midwifery Guild. The Southern Natural Therapies Society, and accredited by the Guild of Bodywork Practitioners.</p>
    <p>Maren is also a Registered Nurse and Midwife. Most of her professional career has been as a midwife, which has included working in the community in the UK, providing ante natal care and classes, intra partum care, home births, and postnatal care in the home. Maren has also worked in the private and public maternity sectors in Perth.</p>
    <p>Maren was introduced to the wonderful benefits of pregnancy and baby massage after a career change. Working as a Practitioner of Pregnancy Massage, and Paediatric Massage Consultant, enables her to continue working with mothers and babies.</p>
  </main>

  <section class="hearts-band" role="img" aria-label="Soft background of scattered pink hearts"></section>
  <div class="cert-badge" role="img" aria-label="Certification badge"></div>
  <div class="social">
    <p class="social-label">Follow us on</p>
    <a class="social-link" href="#"><span class="social-dot"></span>FamilyFeed</a>
  </div>

  <footer class="site-footer">
    <ul class="footer-links">
      <li><a href="#">Home</a></li>
      <li><a href="#">About Me</a></li>
      <li><a href="#">Pregnancy Massage</a></li>
      <li><a href="#">Baby Massage</a></li>
      <li><a href="#">Pricing</a></li>
      <li><a href="#">News</a></li>
      <li><a href="#">Contact Me</a></li>
    </ul>
    <p class="copyright">Copyright &copy; 2017 Willow Cradle Pregnancy &amp; Baby Massage. &nbsp;All rights reserved.</p>
  </footer>
</body>
</html>
```